The Plate Compass

Cutting Through the Noise to What Actually Works.

Nutrition book

Target Market(s)

People looking to be or get healthy and eat right.

```html
<!DOCTYPE html>
<html lang="en">
<head>
<meta charset="utf-8">
<title>The Plate Compass – Book Cover</title>
<link rel="stylesheet" href="https://fonts.googleapis.com/css2?family=Barlow+Condensed:wght@700;800&family=Barlow+Semi+Condensed:wght@500;600;700&display=swap">
<style>
  :root {
    --backdrop: #e9bd52;
    --cover: #f7f7f5;
    --ink: #1c1c1c;
    --title-green: #3f8a2e;
    --title-orange: #e29a1c;
    --photo-skin: #d8a888;
    --photo-top: #ee6a52;
    --produce-green: #5da53a;
    --produce-red: #d8432a;
  }
  html, body {
    margin: 0;
    padding: 0;
    width: 1200px;
    height: 937px;
    overflow: hidden;
    background: var(--backdrop);
  }
  .book-cover {
    position: absolute;
    left: 322px;
    top: 38px;
    width: 574px;
    height: 860px;
    background: var(--cover);
    overflow: hidden;
    box-shadow: 0 10px 30px rgba(0,0,0,0.18);
  }
  .title-block {
    position: absolute;
    left: 40px;
    top: 80px;
    margin: 0;
    font-family: "Barlow Condensed", "Arial Narrow", sans-serif;
    font-weight: 800;
    text-transform: uppercase;
    line-height: 0.9;
  }
  .title-the {
    display: block;
    font-size: 26px;
    color: var(--ink);
    letter-spacing: 1px;
    margin-bottom: 4px;
  }
  .title-main {
    display: block;
    font-size: 118px;
    color: var(--title-green);
    letter-spacing: 1px;
  }
  .title-sub {
    display: block;
    font-size: 100px;
    color: var(--title-orange);
    letter-spacing: 1px;
  }
  .cover-photo {
    position: absolute;
    left: 330px;
    top: 330px;
    width: 220px;
    height: 230px;
    border-radius: 6px;
    background: linear-gradient(180deg, #f1e6df 0%, var(--photo-skin) 40%, var(--photo-top) 62%, #5a4d7a 100%);
  }
  .tagline {
    position: absolute;
    left: 40px;
    top: 345px;
    width: 250px;
    margin: 0;
    font-family: "Barlow Semi Condensed", "Arial Narrow", sans-serif;
    font-weight: 700;
    font-size: 25px;
    line-height: 1.2;
    text-transform: uppercase;
    color: var(--ink);
  }
  .byline {
    position: absolute;
    left: 40px;
    top: 470px;
    font-family: "Barlow Semi Condensed", "Arial Narrow", sans-serif;
    text-transform: uppercase;
    color: var(--ink);
  }
  .byline-label {
    display: block;
    font-weight: 500;
    font-size: 15px;
    letter-spacing: 1px;
  }
  .byline-name {
    display: block;
    font-weight: 700;
    font-size: 23px;
    margin-top: 2px;
  }
  .cover-produce {
    position: absolute;
    left: 170px;
    top: 575px;
    width: 380px;
    height: 250px;
    border-radius: 10px;
    background: radial-gradient(circle at 35% 55%, var(--produce-green) 0%, #7fbf4e 35%, var(--produce-red) 70%, #f0c93a 100%);
  }
</style>
</head>
<body>
  <main class="book-cover">
    <h1 class="title-block">
      <span class="title-the">The</span>
      <span class="title-main">Plate</span>
      <span class="title-sub">Compass</span>
    </h1>

    <div class="cover-photo" role="img" aria-label="Photo of a fit woman in a sports top measuring her waist with a tape measure"></div>

    <p class="tagline">Cutting through the noise to what actually works.</p>

    <div class="byline">
      <span class="byline-label">Written by</span>
      <span class="byline-name">Mara Ellison, MD</span>
    </div>

    <div class="cover-produce" role="img" aria-label="Illustration of fresh produce: watermelon, leafy greens, peppers, tomato, banana, figs, strawberries, kiwi and carrots"></div>
  </main>
</body>
</html>
```